Business card design for a dynamic IT consulting company

We need a business card design for a young firm, specialized in the Telecommunications/Consulting industry. The name of the company is Quindor and Partners Business Consulting Ltd. (Short name: Quindor and Partnes)
Quindor = solve read reverse, so we aim to be uncomplicated and solution-oriented. The small pipe in our logo is also related to the word solve. So we need a new business card design, which is simple, eye catching and something non traditional (I would probably prefer a square shaped design rather than a rectangle, but open for suggestions). Attached our logo.

Target Market(s)

Usually our customers are Tier1 Telecoms providers (Q-Netra, Palorix, etc) and their executives.

Industry/Entity Type

Business

Contact Information for Business Card

Name: Bence Tolnavari
Email: b.tolnavari@quindor.hu
Web: www.quindor.hu
Mobile: +36 30 518 2769
Title: Managing Director

Optional:
Company name: Quindor and Partners Ltd.
Address: 1087 Budapest, Tolvenka str. 28/C, Hungary

Font styles to use
Other font styles liked:
• helveticaneue_medium, Prime Regular are used now.

Colors

Designer to choose colors to be used in the design.

Requirements
Must have
• I would like to have a 2 sided design.
Nice to have
• I thought if we make the logo a bit bigger (without the company name), that could go to the back with the company name below. I though, if the pipe in the logo is somehow touchable on the business card, would be nice and unique.

```html
<!DOCTYPE html>
<html lang="en">
<head>
<meta charset="utf-8">
<title>Quindor and Partners – Business Card</title>
<link href="https://fonts.googleapis.com/css2?family=Exo+2:wght@500&family=Roboto:wght@400&display=swap" rel="stylesheet">
<style>
  :root {
    --page-bg: #e9e9eb;
    --card-bg: #2b2b2d;
    --card-shade: #333336;
    --text-light: #f4f4f4;
    --text-soft: #d8d8d8;
    --accent-blue: #1e9bd7;
    --accent-magenta: #b4308f;
  }
  * { margin: 0; padding: 0; box-sizing: border-box; }
  html, body { width: 1200px; height: 880px; overflow: hidden; }
  body {
    background: var(--page-bg);
    display: flex;
    flex-direction: column;
    align-items: center;
    justify-content: center;
    gap: 44px;
    font-family: "Roboto", Arial, sans-serif;
  }
  .card {
    position: relative;
    width: 620px;
    height: 354px;
    border-radius: 18px;
    background: var(--card-bg);
    overflow: hidden;
    box-shadow: 0 6px 18px rgba(0,0,0,0.18);
  }
  .card-texture {
    position: absolute;
    top: 0; right: 0;
    width: 300px; height: 100%;
    background: linear-gradient(200deg, var(--card-shade) 0%, rgba(51,51,54,0) 70%);
  }
  .brand {
    display: flex;
    align-items: center;
    gap: 14px;
    font-family: "Exo 2", Arial, sans-serif;
    font-weight: 500;
    color: var(--text-light);
    white-space: nowrap;
  }
  .brand-square {
    background: var(--accent-blue);
    flex: none;
  }
  /* Logo side */
  .card-logo-side .brand {
    position: absolute;
    left: 50%; top: 128px;
    transform: translateX(-50%);
    font-size: 44px;
  }
  .card-logo-side .brand-square { width: 20px; height: 20px; }
  .web-line {
    position: absolute;
    left: 0; right: 0; top: 232px;
    text-align: center;
    color: var(--text-soft);
    font-size: 15px;
    letter-spacing: 3px;
  }
  /* Contact side */
  .card-contact-side .brand {
    position: absolute;
    left: 40px; top: 62px;
    font-size: 40px;
  }
  .card-contact-side .brand-square { width: 18px; height: 18px; }
  .divider {
    width: 1px; height: 52px;
    background: var(--text-soft);
  }
  .person {
    position: absolute;
    left: 40px; top: 196px;
  }
  .person-name {
    font-family: "Exo 2", Arial, sans-serif;
    font-weight: 500;
    font-size: 24px;
    color: var(--text-light);
  }
  .person-title {
    font-size: 14px;
    color: var(--accent-blue);
    margin-top: 2px;
  }
  .contact {
    position: absolute;
    left: 40px; top: 276px;
    font-size: 13px;
    color: var(--text-soft);
    line-height: 1.65;
  }
  .contact .label { color: var(--accent-blue); }
  .contact .sep { color: var(--text-light); margin: 0 5px; }
</style>
</head>
<body>
  <section class="card card-logo-side">
    <div class="card-texture" role="img" aria-label="Faint dark geometric texture in the card corner"></div>
    <div class="brand"><span class="brand-square"></span><span>Quindor &amp; Partners</span></div>
    <p class="web-line">www.quindor.hu</p>
  </section>

  <section class="card card-contact-side">
    <div class="card-texture" role="img" aria-label="Faint dark geometric texture in the card corner"></div>
    <div class="brand"><span class="brand-square"></span><span class="divider"></span><span>Quindor &amp; Partners</span></div>
    <div class="person">
      <p class="person-name">Bence Tolnavari</p>
      <p class="person-title">Managing Director</p>
    </div>
    <div class="contact">
      <p><span class="label">M:</span> +36 30 518 2769<span class="sep">|</span><span class="label">E:</span> b.tolnavari@quindor.hu<span class="sep">|</span><span class="label">W:</span> www.quindor.hu</p>
      <p>1087 Budapest, Tolvenka str. 28/C, Hungary</p>
    </div>
  </section>
</body>
</html>
```